NCBG website design

We need a page template website design for a cms website. Please see the brief attached for the details.
The client is the National Copperfleece Breeders Guild which is an organisation promoting the Copperfleece Sheep Breed within Australia.
Updates

Project Deadline Extended
Reason: So that my top few designs can make changes and re-submit.

Target Market(s)

See attached brief

```html
<!DOCTYPE html>
<html lang="en">
<head>
<meta charset="utf-8">
<title>National Copperfleece Breeders Guild</title>
<link rel="stylesheet" href="https://fonts.googleapis.com/css2?family=Lato:wght@400;700&family=Ubuntu:wght@300;400;500;700&display=swap">
<style>
:root{
  --green:#14903f;
  --green-dark:#0e6a2e;
  --nav:#0f7a35;
  --ink:#222;
  --text:#333;
  --grey-dark:#2b2b2b;
  --yellow:#efe01c;
  --card:#f4f4f4;
  --card-border:#cfcfcf;
  --footer:#2a2727;
  --footer-band:#4a4848;
  --footer-text:#d8d8d8;
  --sponsor-red:#e04a2a;
}
*{box-sizing:border-box;margin:0;padding:0}
html,body{width:1120px;height:1200px;overflow:hidden;background:#fff}
body{font-family:'Lato',sans-serif;color:var(--text)}
.page{position:relative;width:1120px;height:1200px;overflow:hidden}

.hero{position:absolute;left:0;top:0;width:1120px;height:319px;
  background:linear-gradient(180deg,#7d6c58 0%,#8c7a5e 35%,#c9a877 60%,#b8925e 85%,#8a6f4b 100%)}

.masthead{position:absolute;left:170px;top:8px;width:780px;height:93px;background:#eeeeee;display:flex;align-items:center}
.brand{display:flex;align-items:center;gap:8px;margin-left:14px;width:200px}
.brand-mark{width:52px;height:52px;border-radius:50%;background:var(--green)}
.brand-name{font-family:'Lato',sans-serif;font-weight:700;font-size:17px;color:var(--green)}
.site-title{font-family:'Ubuntu',sans-serif;font-weight:500;font-size:33px;color:var(--ink);margin-left:12px;white-space:nowrap}

.nav{position:absolute;left:170px;top:101px;width:780px;height:43px;display:flex;background:var(--nav)}
.nav a{display:flex;align-items:center;justify-content:center;color:#fff;text-decoration:none;font-weight:700;font-size:12.5px;text-transform:uppercase;border-right:1px solid rgba(0,0,0,.18);height:100%}
.nav a:last-child{border-right:0}
.nav a.active{background:var(--grey-dark)}
.dropdown{position:absolute;left:244px;top:144px;width:158px;background:var(--grey-dark)}
.dropdown a{display:block;height:40px;line-height:40px;padding-left:12px;color:#fff;text-decoration:none;font-weight:700;font-size:12.5px;text-transform:uppercase}
.dropdown a+a{border-top:1px solid #444;background:#222}

.sidebar{position:absolute;left:168px;top:358px;width:228px}
.card{height:104px;background:var(--card);border:1px solid var(--card-border);border-radius:2px;box-shadow:0 2px 2px rgba(0,0,0,.12);display:flex;align-items:center;padding-left:16px;margin-bottom:9px}
.card-icon{width:72px;height:72px;flex:none}
.card-text{margin-left:6px;font-family:'Ubuntu',sans-serif;font-size:15.5px;color:var(--ink);line-height:19px;text-transform:uppercase}
.card-text small{display:block;font-family:'Lato',sans-serif;font-weight:700;font-size:11px;color:var(--green);line-height:19px}
.sponsors-head{margin-top:3px;height:34px;background:var(--yellow);border-radius:2px;font-family:'Ubuntu',sans-serif;font-weight:500;font-size:15px;line-height:34px;padding-left:11px;color:var(--ink)}
.sponsor{margin:6px 2px 0;width:224px;height:174px;background:var(--sponsor-red);position:relative}
.sponsor-top{padding:5px 0 0 20px;color:#fff;font-family:'Ubuntu',sans-serif}
.sponsor-top span{display:block;font-size:11px}
.sponsor-top b{display:block;font-size:19px;font-weight:700;line-height:20px}
.sponsor-photo{position:absolute;left:0;top:46px;width:224px;height:106px;background:linear-gradient(180deg,#6d7a52 0%,#7b5234 55%,#a89a6c 100%)}
.sponsor-url{position:absolute;left:0;bottom:0;width:224px;height:22px;line-height:22px;text-align:center;color:#fff;font-weight:700;font-size:12.5px}
.view-all{display:block;margin:8px 0 0 4px;font-weight:700;font-size:11px;color:var(--green);text-decoration:none}

.content{position:absolute;left:413px;top:356px;width:536px;font-size:12px;line-height:20.8px}
.welcome{font-family:'Ubuntu',sans-serif;font-weight:300;font-size:29px;line-height:32px;color:var(--ink)}
.content h1{font-family:'Ubuntu',sans-serif;font-weight:500;font-size:29px;line-height:32px;color:var(--green);margin-bottom:8px}
.content h2{font-family:'Ubuntu',sans-serif;font-weight:400;font-size:14.5px;color:var(--green);margin-top:18px;line-height:20px;margin-bottom:2px}
.content a{color:var(--green)}
.ticks{list-style:none}
.ticks li{position:relative;padding-left:16px;line-height:23.2px}
.ticks svg{position:absolute;left:0;top:7px}

.footer{position:absolute;left:0;top:1076px;width:1120px;height:124px;background:var(--footer);border-top:6px solid var(--footer-band);color:var(--footer-text);font-size:11px}
.footer .copy{position:absolute;left:170px;top:26px;line-height:21px}
.footer .copy a{color:var(--green);text-decoration:none}
.footer .follow{position:absolute;left:494px;top:22px;display:flex;align-items:center;gap:10px}
.follow-mark{width:21px;height:21px;background:#3b5998;border-radius:2px}
.footer .contact{position:absolute;left:698px;top:22px;line-height:21px}
.contact-row{display:flex}
.contact-row dt{width:56px}
.contact-row .sep{width:30px}
</style>
</head>
<body>
<div class="page">
  <div class="hero" role="img" aria-label="Photograph of a flock of Copperfleece sheep standing in a paddock"></div>

  <header class="masthead">
    <div class="brand"><span class="brand-mark"></span><span class="brand-name">Copperfleece</span></div>
    <div class="site-title">National Copperfleece Breeders Guild</div>
  </header>

  <nav class="nav">
    <a href="#" style="width:74px">Home</a>
    <a href="#" class="active" style="width:75px">About</a>
    <a href="#" style="width:82px">Search</a>
    <a href="#" style="width:148px">Member Services</a>
    <a href="#" style="width:108px">Stud Pages</a>
    <a href="#" style="width:70px">News</a>
    <a href="#" style="width:66px">Sales</a>
    <a href="#" style="width:68px">Links</a>
    <a href="#" style="width:89px">Contact</a>
  </nav>
  <div class="dropdown">
    <a href="#">Breed</a>
    <a href="#">Genetic Testing</a>
  </div>

  <aside class="sidebar">
    <div class="card">
      <svg class="card-icon" viewBox="0 0 72 72"><circle cx="36" cy="36" r="34" fill="#f0e02a"/><circle cx="36" cy="36" r="31" fill="#4a4a4a"/>
        <path d="M27 24c2-1 4 0 5 2l2 4c1 2 0 3-1 4l-2 1c1 3 4 6 7 7l1-2c1-1 2-2 4-1l4 2c2 1 3 3 2 5l-1 2c-1 2-4 3-7 2-9-3-15-9-18-18-1-3 0-6 2-7z" fill="#fff"/></svg>
      <div class="card-text">Prime Lamb<br>Helpline</div>
    </div>
    <div class="card">
      <svg class="card-icon" viewBox="0 0 72 72"><circle cx="36" cy="36" r="34" fill="#f0e02a"/><circle cx="36" cy="36" r="31" fill="#4a4a4a"/>
        <rect x="20" y="22" width="32" height="30" rx="3" fill="#fff"/><rect x="20" y="22" width="32" height="6" fill="#ddd"/>
        <rect x="26" y="17" width="3" height="8" fill="#fff"/><rect x="43" y="17" width="3" height="8" fill="#fff"/>
        <g fill="#4a4a4a"><rect x="24" y="31" width="5" height="4"/><rect x="31" y="31" width="5" height="4"/><rect x="38" y="31" width="5" height="4"/><rect x="45" y="31" width="4" height="4"/><rect x="24" y="38" width="5" height="4"/><rect x="31" y="38" width="5" height="4"/><rect x="38" y="38" width="5" height="4"/><rect x="45" y="38" width="4" height="4"/><rect x="24" y="45" width="5" height="4"/><rect x="31" y="45" width="5" height="4"/><rect x="38" y="45" width="5" height="4"/></g></svg>
      <div class="card-text">Events</div>
    </div>
    <div class="card">
      <svg class="card-icon" viewBox="0 0 72 72"><circle cx="36" cy="36" r="34" fill="#f0e02a"/><circle cx="36" cy="36" r="31" fill="#4a4a4a"/>
        <circle cx="31" cy="28" r="8" fill="#fff"/><circle cx="45" cy="33" r="6" fill="#fff"/>
        <path d="M16 50c0-9 7-13 15-13s15 4 15 13z" fill="#fff"/><path d="M40 50c0-6 3-9 6-9 5 0 10 3 10 9z" fill="#fff"/></svg>
      <div class="card-text">Members<small>Members Resources</small><small>Webmanager Login</small></div>
    </div>
    <div class="card">
      <svg class="card-icon" viewBox="0 0 72 72"><circle cx="36" cy="36" r="34" fill="#f0e02a"/><circle cx="36" cy="36" r="31" fill="#4a4a4a"/>
        <path d="M18 31h8l18-10v30L26 41h-8z" fill="#fff"/><rect x="24" y="41" width="6" height="10" fill="#fff"/><rect x="47" y="30" width="5" height="12" rx="2" fill="#fff"/></svg>
      <div class="card-text">Latest<br>News</div>
    </div>

    <div class="sponsors-head">SPONSORS</div>
    <div class="sponsor">
      <div class="sponsor-top"><span>FieldPost</span><b>Stockyard</b></div>
      <div class="sponsor-photo" role="img" aria-label="Photograph of beef cattle grazing in a field"></div>
      <div class="sponsor-url">www.fieldpoststock.com.au</div>
    </div>
    <a href="#" class="view-all">VIEW ALL SPONSORS&gt;</a>
  </aside>

  <main class="content">
    <div class="welcome">WELCOME TO</div>
    <h1>National Copperfleece Breeders Guild</h1>
    <p>Lorem ipsum dolor sit amet, consectetur adipiscing elit. Sed quis nisi euismod, fermentum tellus a, lobortis quam. <b>Vestibulum condimentum</b> mi vitae diam tristique, egestas dignissim diam mattis. <a href="#">Curabitur vel diam</a> in massa porttitor dictum id in lorem.</p>

    <h2>Vivamus faucibus ac leo ac dignissim.</h2>
    <p>Maecenas orci est, euismod facilisis feugiat sit amet, semper ut tortor. Donec eleifend accumsan nisl, nec laoreet leo iaculis sit amet. Vivamus varius arcu eu sagittis aliquam. Vivamus accumsan cursus hendrerit. <b>Vivamus eu magna rhoncus</b>, consectetur metus ac, varius lacus.</p>

    <h2>Donec ultricies, tortor quis sagittis sagittis</h2>
    <ul class="ticks">
      <li><svg width="11" height="9" viewBox="0 0 11 9"><path d="M1 4.5l3 3 6-6" stroke="#14903f" stroke-width="2.4" fill="none"/></svg>Mauris erat ullamcorper augue, eu placerat diam nunc a lorem.</li>
      <li><svg width="11" height="9" viewBox="0 0 11 9"><path d="M1 4.5l3 3 6-6" stroke="#14903f" stroke-width="2.4" fill="none"/></svg>Nam vulputate mauris id arcu pharetra, sed posuere quam cursus.</li>
      <li><svg width="11" height="9" viewBox="0 0 11 9"><path d="M1 4.5l3 3 6-6" stroke="#14903f" stroke-width="2.4" fill="none"/></svg>Nullam eget massa vel mi posuere venenatis sed quis tortor.</li>
      <li><svg width="11" height="9" viewBox="0 0 11 9"><path d="M1 4.5l3 3 6-6" stroke="#14903f" stroke-width="2.4" fill="none"/></svg>In hac habitasse platea dictumst. Fusce nisi tellus, fermentum a luctus eget, convallis.</li>
      <li><svg width="11" height="9" viewBox="0 0 11 9"><path d="M1 4.5l3 3 6-6" stroke="#14903f" stroke-width="2.4" fill="none"/></svg>In commodo egestas magna quis placerat. Quisque adipiscing consequat nisi.</li>
    </ul>

    <h2>Cras accumsan orci mauris ut aliquam ipsum faucibus sed.</h2>
    <p>Fusce quam dui, accumsan a magna in, faucibus tristique lectus. Vestibulum sapien leo, placerat quis luctus eget, auctor et justo. Vestibulum ante ipsum primis in faucibus orci luctus et ultrices posuere cubilia Curae; <b>Duis sagittis</b>, risus ut viverra dignissim, lectus nunc iaculis arcu, et gravida est tortor ut erat. Morbi a feugiat dolor, in tristique elit. Mauris feugiat aliquam vulputate. Etiam sed mi quis velit commodo mollis et eu quam. Vestibulum mollis at dolor sed egestas.</p>

    <h2>Vivamus faucibus ac leo ac dignissim.</h2>
    <p>Maecenas orci est, euismod facilisis feugiat sit amet, semper ut tortor. Donec eleifend accumsan nisl, nec laoreet leo iaculis sit amet. Vivamus varius arcu eu sagittis aliquam. Vivamus accumsan cursus hendrerit. Vivamus eu magna rhoncus, consectetur metus ac, varius lacus.</p>
  </main>

  <footer class="footer">
    <div class="copy">Copyright National Copperfleece Breeders Guild<br><a href="#">Website design and development by Brightgate</a></div>
    <div class="follow">Follow us on: <span class="follow-mark"></span></div>
    <dl class="contact">
      <div class="contact-row"><dt>Address</dt><span class="sep">:</span><dd>PO Box 412, Eastfield, SA 5990</dd></div>
      <div class="contact-row"><dt>Phone</dt><span class="sep">:</span><dd>08 5550 1234</dd></div>
      <div class="contact-row"><dt>Fax</dt><span class="sep">:</span><dd>08 5550 1235</dd></div>
      <div class="contact-row"><dt>Email</dt><span class="sep">:</span><dd>info@copperfleece.example</dd></div>
    </dl>
  </footer>
</div>
</body>
</html>
```